Kelvaro.ch is looking for business card letterhead and envelope C5 with WOW effect

We need a strong business card for our company Kelvaro.ch, logo is available. You want a black or dark background on which the logo Stark r% 26 # 252; appears. Letterhead and envelope in C5 format should be in a similar design, but does not have to be We need a strong business card for our company Kelvaro.ch, logo is available. A black or dark background is desired, on which the logo Stark comes across. The letterhead and the envelope in C5 format should have a similar design.

Target Market(s)

Private customers as well as entrepreneurs

Contact Information for Business Card

E-mail: info@kelvaro-example.ch
Web.www.Kelvaro-example.ch
Tel: +41 ( 0 ) 79 482 6037
Adresse:
Lindenweg 14
9406 Tarnbach

Hier kann man Icons verwenden für Email,Tel und Adressse

Font styles to use
Other font styles liked:
• Dubai,bold

Colors

Designer to choose colors to be used in the design.

Requirements
Must have
• WOW effect
Nice to have
• R% 26 # 252; back business card with our service listings. - VEHICLE LABELING - SHOP WINDOW LABELING - STICKERS AND MUCH MORE ... in red color

```html
<!DOCTYPE html>
<html lang="en">
<head>
<meta charset="utf-8">
<title>Kelvaro.ch business card</title>
<link rel="stylesheet" href="https://fonts.googleapis.com/css2?family=Open+Sans:wght@400;600;700;800&family=Ubuntu:wght@400;700&display=swap">
<style>
  :root {
    --backdrop: #4a433d;
    --card: #1c1c1c;
    --card-edge: #262626;
    --white: #f4f4f4;
    --soft: #d8d8d8;
    --yellow: #f7c51e;
    --red: #e0141e;
  }
  * { margin: 0; padding: 0; box-sizing: border-box; }
  html, body { width: 1200px; height: 930px; overflow: hidden; }
  body {
    background: var(--backdrop);
    font-family: "Open Sans", sans-serif;
    position: relative;
  }
  .card {
    position: absolute;
    width: 600px;
    height: 343px;
    border-radius: 18px;
    background: linear-gradient(120deg, var(--card-edge) 0%, var(--card) 55%, #151515 100%);
    box-shadow: 0 14px 30px rgba(0,0,0,.45);
    overflow: hidden;
    color: var(--white);
  }
  .card--front { left: 70px; top: 70px; }
  .card--back { left: 530px; top: 520px; }

  /* front */
  .brand {
    position: absolute;
    left: 70px;
    top: 118px;
    display: flex;
    align-items: center;
    gap: 16px;
  }
  .brand__mark { width: 22px; height: 22px; background: var(--yellow); }
  .brand__name {
    font-family: "Open Sans", sans-serif;
    font-weight: 800;
    font-size: 52px;
    letter-spacing: 1px;
    text-transform: uppercase;
    color: var(--white);
    line-height: 1;
  }
  .services {
    position: absolute;
    right: 70px;
    top: 200px;
    list-style: none;
    text-align: right;
  }
  .services li {
    font-size: 15px;
    line-height: 20px;
    text-transform: uppercase;
    color: var(--white);
    display: flex;
    justify-content: flex-end;
    align-items: center;
    gap: 10px;
  }
  .services li:nth-child(2) { margin-right: 14px; }
  .services li:nth-child(3) { margin-right: 28px; }
  .services li:first-child { margin-right: 0; }
  .services .dot {
    width: 9px; height: 9px;
    border: 2px solid var(--red);
    border-radius: 50%;
    flex: none;
  }

  /* back */
  .accent-bar {
    position: absolute;
    right: 0;
    top: 26px;
    width: 14px;
    height: 34px;
    background: var(--yellow);
  }
  .person {
    position: absolute;
    right: 36px;
    top: 24px;
    text-align: right;
  }
  .person__name {
    font-family: "Ubuntu", sans-serif;
    font-weight: 700;
    font-size: 28px;
    letter-spacing: 2px;
    text-transform: uppercase;
  }
  .person__name .surname { color: var(--yellow); }
  .person__role { font-size: 14px; color: var(--soft); margin-top: 2px; }
  .contacts {
    position: absolute;
    right: 36px;
    top: 150px;
    list-style: none;
    text-align: right;
  }
  .contacts li {
    font-family: "Ubuntu", sans-serif;
    font-size: 16px;
    line-height: 23px;
    display: flex;
    justify-content: flex-end;
    align-items: center;
    gap: 10px;
  }
  .contacts svg { width: 13px; height: 13px; flex: none; }
  .divider {
    position: absolute;
    right: 36px;
    top: 232px;
    width: 38px;
    height: 2px;
    background: var(--yellow);
  }
  .address {
    position: absolute;
    right: 36px;
    top: 246px;
    font-family: "Ubuntu", sans-serif;
    font-size: 16px;
  }
  .pattern-area {
    position: absolute;
    left: 50px;
    top: 110px;
    width: 330px;
    height: 210px;
    border-radius: 14px;
    background: radial-gradient(ellipse at 40% 45%, #3a3a3a 0%, #2a2a2a 45%, rgba(28,28,28,0) 78%);
  }
</style>
</head>
<body>

<section class="card card--front" aria-label="Business card front">
  <div class="brand">
    <span class="brand__mark"></span>
    <span class="brand__name">Kelvaro.ch</span>
  </div>
  <ul class="services">
    <li>Vehicle labeling <span class="dot"></span></li>
    <li>Shop window labeling <span class="dot"></span></li>
    <li>Stickers and much more <span class="dot"></span></li>
  </ul>
</section>

<section class="card card--back" aria-label="Business card back">
  <div class="accent-bar"></div>
  <div class="person">
    <p class="person__name">Jonas <span class="surname">Reber</span></p>
    <p class="person__role">Director</p>
  </div>

  <div class="pattern-area" role="img" aria-label="Decorative embossed brand pattern in dark grey"></div>

  <ul class="contacts">
    <li>+41 ( 0 ) 79 482 6037
      <svg viewBox="0 0 24 24" aria-hidden="true"><path fill="#f7c51e" d="M6.6 10.8a15.1 15.1 0 0 0 6.6 6.6l2.2-2.2a1 1 0 0 1 1-.25 11.4 11.4 0 0 0 3.6.57 1 1 0 0 1 1 1V20a1 1 0 0 1-1 1A17 17 0 0 1 3 4a1 1 0 0 1 1-1h3.5a1 1 0 0 1 1 1c0 1.25.2 2.45.57 3.57a1 1 0 0 1-.25 1z"/></svg>
    </li>
    <li>info@kelvaro-example.ch
      <svg viewBox="0 0 24 24" aria-hidden="true"><rect x="2.5" y="5" width="19" height="14" rx="1.5" fill="none" stroke="#f7c51e" stroke-width="2.2"/><path d="M3 6l9 7 9-7" fill="none" stroke="#f7c51e" stroke-width="2.2"/></svg>
    </li>
    <li>www.Kelvaro-example.ch
      <svg viewBox="0 0 24 24" aria-hidden="true"><circle cx="12" cy="12" r="9.5" fill="none" stroke="#f7c51e" stroke-width="2.2"/><path d="M2.5 12h19M12 2.5c3 3 3 16 0 19M12 2.5c-3 3-3 16 0 19" fill="none" stroke="#f7c51e" stroke-width="1.8"/></svg>
    </li>
  </ul>
  <div class="divider"></div>
  <p class="address">Lindenweg 14 9406 Tarnbach</p>
</section>

</body>
</html>
```